BRIGHTHOLD PROPERTY MANAGEMENT INC. WEBSITE

Please make the website more family-friendly.

I want a website to help me build my property management business by adding listing properties and creating an online application. Im open to any other ideas.
I want a WordPress designer to code it.

Here is my current website. www.brighthold.biz

IDEA: I like the website design https://www.pelicanclimateservices.com/

Thank you

Tom

Number of Pages Required

5+ page

```html
<!DOCTYPE html>
<html lang="en">
<head>
<meta charset="utf-8">
<title>Brighthold Property Management Inc.</title>
<link rel="stylesheet" href="https://fonts.googleapis.com/css2?family=Marcellus&family=Montserrat:wght@400;500;600;700&display=swap">
<style>
:root{
  --red:#a8191e;
  --red-dark:#6e0f12;
  --ink:#141414;
  --grey-bg:#f2f2f4;
  --text:#555;
  --white:#fff;
  --serif:"Marcellus", Georgia, serif;
  --sans:"Montserrat", Arial, sans-serif;
}
*{box-sizing:border-box;margin:0;padding:0}
html,body{width:1200px;height:4220px;overflow:hidden}
body{position:relative;background:var(--white);font-family:var(--sans);color:var(--ink)}
.abs{position:absolute}
a{color:inherit;text-decoration:none}

/* header */
.brand{position:absolute;display:flex;align-items:center;gap:14px;font-family:var(--serif);letter-spacing:3px}
.brand .mark{width:34px;height:34px;background:var(--red)}
.site-brand{left:40px;top:52px;font-size:34px;color:var(--red)}
.topbar{left:340px;top:0;width:860px;height:58px;background:var(--red);clip-path:polygon(40px 0,100% 0,100% 100%,0 100%)}
.topbar .phone{position:absolute;top:18px;color:var(--white);font-size:16px;font-weight:600;display:flex;align-items:center;gap:10px}
.contact-btn{position:absolute;right:24px;top:12px;width:200px;height:36px;background:var(--white);color:var(--red);font-size:14px;font-weight:700;display:flex;align-items:center;justify-content:center;letter-spacing:1px}
.main-nav{left:400px;top:98px;display:flex;gap:30px;font-size:16px;font-weight:700;color:var(--ink)}
.main-nav span::after{content:" ▾";font-size:11px;color:var(--red)}

/* hero */
.hero-photo{left:0;top:160px;width:1200px;height:610px;background:linear-gradient(160deg,#cfe3f0 0%,#8fb3c6 35%,#4f6e7b 60%,#2d3a33 100%)}
.call-tag{left:120px;top:268px;width:200px;height:46px;background:var(--ink);color:var(--white);font-weight:700;font-size:15px;display:flex;align-items:center;padding-left:30px;letter-spacing:1px}
.hero-title{left:120px;top:360px;width:600px;font-family:var(--serif);color:var(--white);font-size:40px;line-height:1.25;letter-spacing:1px}
.estimate{left:828px;top:282px;width:372px;height:238px;background:var(--red);padding:34px 36px}
.estimate h2{font-family:var(--serif);font-weight:400;color:var(--white);font-size:28px;letter-spacing:2px}
.estimate .field{margin-top:22px;height:46px;border:2px solid var(--white);color:var(--white);font-size:13px;font-weight:600;display:flex;align-items:center;padding-left:16px}
.estimate .btn{margin-top:14px;height:46px;background:var(--white);color:var(--red);font-size:16px;font-weight:700;display:flex;align-items:center;justify-content:center;letter-spacing:1px}
.info-cards{left:0;top:590px;width:808px;height:178px;display:flex;gap:4px}
.info-card{flex:1;background:var(--white);padding:28px 26px;box-shadow:0 4px 14px rgba(0,0,0,.12)}
.info-card svg{width:44px;height:44px}
.info-card h3{margin-top:12px;font-size:15px;font-weight:600}
.read-more{margin-top:16px;font-size:13px;font-weight:700;color:var(--red)}

/* about */
.about-photo{left:112px;top:860px;width:490px;height:550px;background:linear-gradient(180deg,#c9d3db 0%,#8595a1 40%,#3d4249 70%,#c99a4c 100%);clip-path:polygon(0 26%,100% 0,100% 100%,0 100%)}
.about-title{left:672px;top:866px;width:500px;font-family:var(--serif);color:var(--red);font-size:32px;line-height:1.3;letter-spacing:1px;font-weight:400}
.about-copy{left:672px;top:1018px;width:480px;font-size:16px;line-height:1.85;color:var(--text)}
.about-copy p+p{margin-top:18px}
.learn-btn{left:690px;top:1336px;width:220px;height:58px;background:var(--red);color:var(--white);font-weight:700;font-size:17px;display:flex;align-items:center;justify-content:center;letter-spacing:1px;box-shadow:-10px 10px 0 var(--ink)}

/* section titles */
.sec-title{position:absolute;left:0;width:1200px;text-align:center;font-family:var(--serif);font-size:30px;letter-spacing:1px;color:var(--red);font-weight:400}

/* weather */
.weather{left:0;top:1500px;width:1200px;height:290px;background:var(--grey-bg)}
.weather-row{left:108px;top:1630px;width:1000px;display:flex;align-items:center}
.weather-row .city{margin-left:20px;font-family:var(--serif);color:var(--red);font-size:26px}
.weather-row .temp{font-size:22px;font-weight:600;margin-top:6px}
.weather-row .stat{position:absolute;top:44px;font-size:16px;font-weight:600;color:#333}

/* listings */
.listings-bg{left:0;top:1760px;width:1200px;height:660px}
.listing{position:absolute;top:2000px;width:440px;height:318px}
.listing .img{width:100%;height:100%}
.listing .cap{position:absolute;left:22px;bottom:38px;color:var(--white);font-size:18px;font-weight:600;line-height:1.5;width:320px}
.listing .go{position:absolute;right:18px;bottom:36px;width:36px;height:36px;border-radius:50%;background:var(--white)}

/* rates */
.rate{position:absolute;top:2572px;width:232px;height:250px;background:var(--ink)}
.rate .head{height:82px;background:var(--grey-bg);clip-path:polygon(0 0,100% 0,100% 78%,50% 100%,0 78%);font-family:var(--serif);color:var(--red);font-size:22px;display:flex;align-items:center;justify-content:center;padding-bottom:12px}
.rate .name{margin-top:50px;text-align:center;color:var(--white);font-size:15px;font-weight:700}
.rate .val{margin-top:16px;text-align:center;color:var(--white);font-size:30px;font-weight:600}

/* areas */
.areas{left:0;top:2880px;width:1200px;height:850px;background:var(--grey-bg)}
.area-box{left:100px;top:3040px;width:980px;height:710px;background:var(--white);padding:50px 36px}
.area-cols{display:flex;gap:0}
.area-cols ul{list-style:none;width:245px}
.area-cols li{font-size:15px;font-weight:600;height:36px;display:flex;align-items:center;gap:10px}
.area-cols li svg{width:14px;height:18px;flex:none}
.map{left:140px;top:3392px;width:900px;height:340px;background:linear-gradient(180deg,#d6e4ea,#cbdbc8 55%,#e7e2d3)}

/* footer */
.footer{left:0;top:3720px;width:1200px;height:440px}
.foot-brand{left:110px;top:3990px;font-size:34px;color:var(--white)}
.foot-links{left:506px;top:3840px;list-style:none;color:var(--white);font-size:15px;font-weight:600;line-height:36px}
.foot-contact{left:848px;top:3840px;color:var(--white);font-size:15px;font-weight:600;line-height:36px}
.bottom-bar{left:0;top:4160px;width:1200px;height:60px;background:var(--ink);color:var(--white);font-size:13px;display:flex;align-items:center;padding-left:110px}
.badges{position:absolute;right:60px;top:16px;display:flex;gap:10px}
.badges span{width:28px;height:28px;background:#ddd}
</style>
</head>
<body>

<!-- header -->
<div class="brand site-brand"><span class="mark"></span>BRIGHTHOLD</div>
<div class="abs topbar">
  <div class="phone" style="left:160px">
    <svg width="16" height="16" viewBox="0 0 24 24"><path fill="#fff" d="M6.6 10.8a15 15 0 0 0 6.6 6.6l2.2-2.2c.3-.3.7-.4 1-.2 1.1.4 2.3.6 3.6.6.6 0 1 .4 1 1V20c0 .6-.4 1-1 1A17 17 0 0 1 3 4c0-.6.4-1 1-1h3.5c.6 0 1 .4 1 1 0 1.3.2 2.5.6 3.6.1.3 0 .7-.2 1z"/></svg>(555) 010-4820</div>
  <div class="phone" style="left:400px">
    <svg width="16" height="16" viewBox="0 0 24 24"><path fill="#fff" d="M6.6 10.8a15 15 0 0 0 6.6 6.6l2.2-2.2c.3-.3.7-.4 1-.2 1.1.4 2.3.6 3.6.6.6 0 1 .4 1 1V20c0 .6-.4 1-1 1A17 17 0 0 1 3 4c0-.6.4-1 1-1h3.5c.6 0 1 .4 1 1 0 1.3.2 2.5.6 3.6.1.3 0 .7-.2 1z"/></svg>(555) 010-4821</div>
  <a class="contact-btn">CONTACT US</a>
</div>
<nav class="abs main-nav"><span>LISTINGS</span><span>OWNERS</span><span>PROSPECT TENANTS</span><span>ABOUT</span><span>COMMUNITY</span><span>MORTGAGE INFO</span></nav>

<!-- hero -->
<div class="abs hero-photo" role="img" aria-label="Photo of a modern family house under a blue sky"></div>
<div class="abs call-tag">CALL TODAY</div>
<h1 class="abs hero-title" style="font-weight:400">GET 1 MONTH PROPERTY MANAGEMENT FEE OFF $120 VALUE!!</h1>
<form class="abs estimate">
  <h2>GET A ESTIMATE</h2>
  <div class="field">ENTER ADDRESS</div>
  <div class="btn">SEARCH NOW</div>
</form>
<div class="abs info-cards">
  <div class="info-card">
    <svg viewBox="0 0 44 44" fill="none" stroke="#a8191e" stroke-width="2.4"><rect x="8" y="5" width="26" height="34" rx="2"/><path d="M14 14h14M14 21h14M14 28h8"/></svg>
    <h3>TENANT APPLICATION</h3><div class="read-more">READ MORE →</div>
  </div>
  <div class="info-card">
    <svg viewBox="0 0 44 44" fill="none" stroke="#a8191e" stroke-width="2.4"><path d="M6 22 22 8l16 14"/><path d="M11 19v17h22V19"/><path d="M19 36V26h6v10"/></svg>
    <h3>RESIDENTS</h3><div class="read-more">READ MORE →</div>
  </div>
  <div class="info-card">
    <svg viewBox="0 0 44 44" fill="none" stroke="#a8191e" stroke-width="2.4"><rect x="6" y="8" width="32" height="26" rx="2"/><circle cx="17" cy="19" r="4"/><path d="M11 30c1-4 4-6 6-6s5 2 6 6M27 17h6M27 23h6"/></svg>
    <h3>PROSPECT INFORMATION</h3><div class="read-more">READ MORE →</div>
  </div>
</div>

<!-- about -->
<div class="abs about-photo" role="img" aria-label="Photo of a modern home with lit garage at dusk"></div>
<h2 class="abs about-title">PROPERTY MANAGEMENT EL GROVE, SACRAMENTO &amp; SURROUNDING AREAS</h2>
<div class="abs about-copy">
  <p>Having the right property manager means having an agent who is committed to helping you and making being a home provider hassle free. I believe clear communication, work ethic, time management, staying focused and knowledge goes a long way in my business.</p>
  <p>This commitment level has helped us build a remarkable track record.</p>
</div>
<a class="abs learn-btn">LEARN MORE</a>

<!-- weather -->
<div class="abs weather"></div>
<h2 class="sec-title" style="top:1560px">LOCAL WEATHER</h2>
<div class="abs weather-row">
  <svg width="70" height="60" viewBox="0 0 70 60"><circle cx="42" cy="20" r="11" fill="#f5b301"/><path d="M18 44a10 10 0 0 1 2-20 14 14 0 0 1 27 4 8 8 0 0 1 0 16z" fill="#8cc3e8"/><path d="M22 50l-3 6M32 50l-3 6M42 50l-3 6" stroke="#4a90c8" stroke-width="3"/></svg>
  <div><div class="city">SACRAMENTO</div><div class="temp">59.76OF</div></div>
  <div class="stat" style="left:530px">CLEAR SKY</div>
  <div class="stat" style="left:688px">HUMIDITY: 71%</div>
  <div class="stat" style="left:868px">WIND: 150 11.5MPH</div>
</div>

<!-- listings -->
<svg class="abs listings-bg" viewBox="0 0 1200 660" preserveAspectRatio="none">
  <rect width="1200" height="660" fill="#a8191e"/>
  <polygon points="0,0 420,0 0,120" fill="#1a1a1a"/>
  <polygon points="1200,0 700,0 1200,110" fill="#1a1a1a"/>
  <polygon points="0,0 1200,0 1200,40 600,70 0,40" fill="#f2f2f4"/>
  <polygon points="0,560 1200,660 0,660" fill="#8f1519"/>
</svg>
<h2 class="sec-title" style="top:1898px;color:#fff">FEATURED LISTINGS</h2>
<div class="listing" style="left:144px">
  <div class="img" role="img" aria-label="Photo of a backyard accessory dwelling unit with trees" style="background:linear-gradient(180deg,#5f87b3,#486a4e 55%,#2a2f2a)"></div>
  <div class="cap">FANTASIC OPPORTUNITY !!<br>1 BDRM X 1 BTH ADU UNIT</div><div class="go"></div>
</div>
<div class="listing" style="left:608px">
  <div class="img" role="img" aria-label="Photo of a bright bedroom interior with a for-rent sign" style="background:linear-gradient(180deg,#ede7de,#d9cfc2 60%,#b6a694)"></div>
  <div class="cap">1 BATHS</div><div class="go"></div>
</div>

<!-- rates -->
<h2 class="sec-title" style="top:2462px">MORTGAGE RATES</h2>
<div class="rate" style="left:112px"><div class="head">AVERAGE RATE*</div><div class="name">30-YEAR FHA RATE</div><div class="val">7.07%</div></div>
<div class="rate" style="left:360px"><div class="head">AVERAGE RATE*</div><div class="name">30-YEAR FIXED RATE</div><div class="val">7.31%</div></div>
<div class="rate" style="left:608px"><div class="head">AVERAGE RATE*</div><div class="name">20-YEAR FIXED RATE</div><div class="val">7.19%</div></div>
<div class="rate" style="left:852px"><div class="head">AVERAGE RATE*</div><div class="name">15-YEAR FIXED RATE</div><div class="val"></div></div>

<!-- areas -->
<div class="abs areas"></div>
<h2 class="sec-title" style="top:2938px">AREAS WE SERVED</h2>
<div class="abs area-box">
  <div class="area-cols">
    <ul><li><svg viewBox="0 0 14 18"><path d="M7 0a7 7 0 0 0-7 7c0 5 7 11 7 11s7-6 7-11a7 7 0 0 0-7-7zm0 10a3 3 0 1 1 0-6 3 3 0 0 1 0 6z" fill="#a8191e"/></svg>SACRAMENTO</li><li><svg viewBox="0 0 14 18"><path d="M7 0a7 7 0 0 0-7 7c0 5 7 11 7 11s7-6 7-11a7 7 0 0 0-7-7zm0 10a3 3 0 1 1 0-6 3 3 0 0 1 0 6z" fill="#a8191e"/></svg>ANTELOPE</li><li><svg viewBox="0 0 14 18"><path d="M7 0a7 7 0 0 0-7 7c0 5 7 11 7 11s7-6 7-11a7 7 0 0 0-7-7zm0 10a3 3 0 1 1 0-6 3 3 0 0 1 0 6z" fill="#a8191e"/></svg>CARMICHAEL</li><li><svg viewBox="0 0 14 18"><path d="M7 0a7 7 0 0 0-7 7c0 5 7 11 7 11s7-6 7-11a7 7 0 0 0-7-7zm0 10a3 3 0 1 1 0-6 3 3 0 0 1 0 6z" fill="#a8191e"/></svg>CITRUS HEIGHTS</li><li><svg viewBox="0 0 14 18"><path d="M7 0a7 7 0 0 0-7 7c0 5 7 11 7 11s7-6 7-11a7 7 0 0 0-7-7zm0 10a3 3 0 1 1 0-6 3 3 0 0 1 0 6z" fill="#a8191e"/></svg>EL DORADO COUNTY</li><li><svg viewBox="0 0 14 18"><path d="M7 0a7 7 0 0 0-7 7c0 5 7 11 7 11s7-6 7-11a7 7 0 0 0-7-7zm0 10a3 3 0 1 1 0-6 3 3 0 0 1 0 6z" fill="#a8191e"/></svg>EL DORADO HILLS</li><li><svg viewBox="0 0 14 18"><path d="M7 0a7 7 0 0 0-7 7c0 5 7 11 7 11s7-6 7-11a7 7 0 0 0-7-7zm0 10a3 3 0 1 1 0-6 3 3 0 0 1 0 6z" fill="#a8191e"/></svg>ELVERTA</li></ul>
    <ul><li><svg viewBox="0 0 14 18"><path d="M7 0a7 7 0 0 0-7 7c0 5 7 11 7 11s7-6 7-11a7 7 0 0 0-7-7zm0 10a3 3 0 1 1 0-6 3 3 0 0 1 0 6z" fill="#a8191e"/></svg>FAIR OAKS</li><li><svg viewBox="0 0 14 18"><path d="M7 0a7 7 0 0 0-7 7c0 5 7 11 7 11s7-6 7-11a7 7 0 0 0-7-7zm0 10a3 3 0 1 1 0-6 3 3 0 0 1 0 6z" fill="#a8191e"/></svg>FOLSOM</li><li><svg viewBox="0 0 14 18"><path d="M7 0a7 7 0 0 0-7 7c0 5 7 11 7 11s7-6 7-11a7 7 0 0 0-7-7zm0 10a3 3 0 1 1 0-6 3 3 0 0 1 0 6z" fill="#a8191e"/></svg>FOOTHILL FARMS</li><li><svg viewBox="0 0 14 18"><path d="M7 0a7 7 0 0 0-7 7c0 5 7 11 7 11s7-6 7-11a7 7 0 0 0-7-7zm0 10a3 3 0 1 1 0-6 3 3 0 0 1 0 6z" fill="#a8191e"/></svg>FLORIN VICINITY</li><li><svg viewBox="0 0 14 18"><path d="M7 0a7 7 0 0 0-7 7c0 5 7 11 7 11s7-6 7-11a7 7 0 0 0-7-7zm0 10a3 3 0 1 1 0-6 3 3 0 0 1 0 6z" fill="#a8191e"/></svg>LAND PARK</li><li><svg viewBox="0 0 14 18"><path d="M7 0a7 7 0 0 0-7 7c0 5 7 11 7 11s7-6 7-11a7 7 0 0 0-7-7zm0 10a3 3 0 1 1 0-6 3 3 0 0 1 0 6z" fill="#a8191e"/></svg>GALT</li><li><svg viewBox="0 0 14 18"><path d="M7 0a7 7 0 0 0-7 7c0 5 7 11 7 11s7-6 7-11a7 7 0 0 0-7-7zm0 10a3 3 0 1 1 0-6 3 3 0 0 1 0 6z" fill="#a8191e"/></svg>LAGUNA</li></ul>
    <ul><li><svg viewBox="0 0 14 18"><path d="M7 0a7 7 0 0 0-7 7c0 5 7 11 7 11s7-6 7-11a7 7 0 0 0-7-7zm0 10a3 3 0 1 1 0-6 3 3 0 0 1 0 6z" fill="#a8191e"/></svg>MATHER</li><li><svg viewBox="0 0 14 18"><path d="M7 0a7 7 0 0 0-7 7c0 5 7 11 7 11s7-6 7-11a7 7 0 0 0-7-7zm0 10a3 3 0 1 1 0-6 3 3 0 0 1 0 6z" fill="#a8191e"/></svg>NATOMAS</li><li><svg viewBox="0 0 14 18"><path d="M7 0a7 7 0 0 0-7 7c0 5 7 11 7 11s7-6 7-11a7 7 0 0 0-7-7zm0 10a3 3 0 1 1 0-6 3 3 0 0 1 0 6z" fill="#a8191e"/></svg>NORTH HIGHLANDS</li><li><svg viewBox="0 0 14 18"><path d="M7 0a7 7 0 0 0-7 7c0 5 7 11 7 11s7-6 7-11a7 7 0 0 0-7-7zm0 10a3 3 0 1 1 0-6 3 3 0 0 1 0 6z" fill="#a8191e"/></svg>ORANGEVALE</li><li><svg viewBox="0 0 14 18"><path d="M7 0a7 7 0 0 0-7 7c0 5 7 11 7 11s7-6 7-11a7 7 0 0 0-7-7zm0 10a3 3 0 1 1 0-6 3 3 0 0 1 0 6z" fill="#a8191e"/></svg>RANCHO CORDOVA</li><li><svg viewBox="0 0 14 18"><path d="M7 0a7 7 0 0 0-7 7c0 5 7 11 7 11s7-6 7-11a7 7 0 0 0-7-7zm0 10a3 3 0 1 1 0-6 3 3 0 0 1 0 6z" fill="#a8191e"/></svg>RANCHO CORDOVA</li><li><svg viewBox="0 0 14 18"><path d="M7 0a7 7 0 0 0-7 7c0 5 7 11 7 11s7-6 7-11a7 7 0 0 0-7-7zm0 10a3 3 0 1 1 0-6 3 3 0 0 1 0 6z" fill="#a8191e"/></svg>RANCHO MURIETA</li></ul>
    <ul><li><svg viewBox="0 0 14 18"><path d="M7 0a7 7 0 0 0-7 7c0 5 7 11 7 11s7-6 7-11a7 7 0 0 0-7-7zm0 10a3 3 0 1 1 0-6 3 3 0 0 1 0 6z" fill="#a8191e"/></svg>RIO LINDA</li><li><svg viewBox="0 0 14 18"><path d="M7 0a7 7 0 0 0-7 7c0 5 7 11 7 11s7-6 7-11a7 7 0 0 0-7-7zm0 10a3 3 0 1 1 0-6 3 3 0 0 1 0 6z" fill="#a8191e"/></svg>ROCKLIN</li><li><svg viewBox="0 0 14 18"><path d="M7 0a7 7 0 0 0-7 7c0 5 7 11 7 11s7-6 7-11a7 7 0 0 0-7-7zm0 10a3 3 0 1 1 0-6 3 3 0 0 1 0 6z" fill="#a8191e"/></svg>ROSEMONT</li><li><svg viewBox="0 0 14 18"><path d="M7 0a7 7 0 0 0-7 7c0 5 7 11 7 11s7-6 7-11a7 7 0 0 0-7-7zm0 10a3 3 0 1 1 0-6 3 3 0 0 1 0 6z" fill="#a8191e"/></svg>ROSEVILLE</li><li><svg viewBox="0 0 14 18"><path d="M7 0a7 7 0 0 0-7 7c0 5 7 11 7 11s7-6 7-11a7 7 0 0 0-7-7zm0 10a3 3 0 1 1 0-6 3 3 0 0 1 0 6z" fill="#a8191e"/></svg>WEST SACRAMENTO</li></ul>
  </div>
</div>
<div class="abs map" role="img" aria-label="Map showing the Sacramento service area"></div>

<!-- footer -->
<svg class="abs footer" viewBox="0 0 1200 440" preserveAspectRatio="none">
  <rect width="1200" height="440" fill="#a8191e"/>
  <polygon points="0,0 1200,0 1200,20 0,90" fill="#141414"/>
  <polygon points="0,0 1200,0 1200,10 0,30" fill="#f2f2f4"/>
</svg>
<div class="brand foot-brand"><span class="mark" style="background:#fff"></span>BRIGHTHOLD</div>
<ul class="abs foot-links"><li>LISTINGS</li><li>OWNERS</li><li>PROSPECT TENANTS</li><li>ABOUT</li><li>COMMUNITY</li><li>MORTGAGE INFO</li></ul>
<div class="abs foot-contact">PHONE:(555) 010-4821<br>MOBILE:(555) 010-4821<br>BRE# 02245178<br>4400 ALDER CREEK RD. #118<br>SACRAMENTO , CA 95822</div>
<div class="abs bottom-bar">COPYRIGHT© 2024 BRIGHTHOLD PROPERTY MANAGEMENT INC.
  <div class="badges"><span></span><span></span><span></span><span></span></div>
</div>

</body>
</html>
```